Where the Lantern Fades: A Sacred Wandering

This is a memoir about my breakdown/breakthrough followed by a spiritual awakening in 2012, I found my guru Harsh Omveli Dev, Mother Ayahuasca, and my spiritual mother, Ishu. By 2013, I was headed for a spiritual adventure through India, Southeast India, and Nepal which lasted 14 months. I lived in ashrams, meditated and prayed in temples,, traveled by train and bus, met many enlightened beings and interesting people. During Vipassana, I discovered my true essence- the light of my soul. It is a book of travel, romance, and spiritual growth. My idea is a road lined with temples, etc. I am walking down the road and see myself at the end of the road, facing out, with a bright star in my heart center. I see the colors in muted yellows and other earth-tone hues. Marigolds are used everywhere in the temples to adorn statues and doorways and this speaks to me. The title of the book is about finding out who I am beyond my stories and it is also about how our story will reveal to us who we really are.

Target Market(s)

Spiritual seekers, adventurers, travelers

Industry/Entity Type

Spiritual

Font styles to use
Serif
Sans Serif
Other font styles liked:
• I’m open. I like simplicity

Colors
FFC000
F8CF3A
FAE287
FDF2CF
FEFAEE

Requirements
Must have
• My name: Carla Serena Tovi, Earth tones, pastels, me or a likeness of me, room for ISBN on back cover
Nice to have
• In the photo uploads I drew an idea of what I would like, there is also the idea in the book
Should not have
• I am not a fan of bright colors and that's all I can select here. I like neutral colors, like browns, slate, creams, and whites. This reflects the dusty roads I took throughout my journey.

```html
<!DOCTYPE html>
<html lang="en">
<head>
<meta charset="utf-8">
<title>Where the Lantern Fades — Cover Wrap</title>
<link rel="stylesheet" href="https://fonts.googleapis.com/css2?family=Cinzel:wght@400;500&family=Montserrat:ital,wght@0,600;0,700;1,700&family=Josefin+Sans:wght@600&display=swap">
<style>
  :root {
    --cream: #fdf6e4;
    --white: #ffffff;
    --yellow: #fff04a;
    --sky-deep: #1d2a4a;
    --sky-teal: #2f5f66;
    --dusk-rose: #b06a72;
    --dusk-amber: #e8a05a;
    --road-brown: #3b2a22;
    --earth-dark: #120d0b;
    --temple-red: #6b2a22;
  }
  * { margin: 0; padding: 0; box-sizing: border-box; }
  html, body { width: 1200px; height: 859px; overflow: hidden; background: var(--earth-dark); }
  .cover {
    position: relative; width: 1200px; height: 859px; overflow: hidden;
  }
  .cover-art {
    position: absolute; inset: 0;
    background:
      radial-gradient(ellipse 260px 200px at 905px 460px, rgba(248,207,58,.55), transparent 70%),
      linear-gradient(90deg, rgba(18,13,11,.15) 0%, rgba(18,13,11,.35) 46%, rgba(18,13,11,.55) 50%, rgba(18,13,11,.1) 54%, transparent 100%),
      linear-gradient(180deg, var(--sky-deep) 0%, var(--sky-teal) 18%, var(--dusk-rose) 32%, var(--dusk-amber) 48%, var(--temple-red) 58%, var(--road-brown) 74%, var(--earth-dark) 100%);
  }
  .back-cover, .spine, .front-cover { position: absolute; top: 0; height: 859px; }
  .back-cover { left: 0; width: 570px; }
  .spine { left: 570px; width: 44px; }
  .front-cover { left: 614px; width: 586px; }

  .title { font-family: "Cinzel", serif; color: var(--cream); text-align: center; font-weight: 400; }
  .title span { display: block; }
  .back-title { position: absolute; left: 0; width: 580px; top: 16px; }
  .back-title .t1 { font-size: 54px; line-height: 50px; }
  .back-title .t2 { font-size: 50px; line-height: 50px; }
  .back-title .t3 { font-size: 84px; line-height: 86px; }

  .blurbs { position: absolute; left: 57px; width: 466px; top: 222px; list-style: none;
    font-family: "Montserrat", sans-serif; font-weight: 700; font-size: 13.6px; line-height: 17.4px; color: var(--white); text-align: justify; }
  .blurbs li { position: relative; padding-left: 10px; margin-bottom: 46px; }
  .blurbs li::before { content: "•"; position: absolute; left: 0; }
  .blurbs li.highlight { color: var(--yellow); font-style: italic; margin-bottom: 30px; }

  .divider { position: absolute; left: 259px; top: 469px; width: 61px; height: 2px; background: var(--white); }
  .about-heading { position: absolute; left: 84px; top: 484px; font-family: "Montserrat", sans-serif; font-weight: 700;
    font-size: 37px; letter-spacing: 1px; color: var(--white); }
  .author-photo { position: absolute; left: 81px; top: 528px; width: 125px; height: 152px;
    background: linear-gradient(180deg, #a7a89a 0%, #c9b3a0 45%, #e7e2da 100%); }
  .author-bio { position: absolute; left: 220px; top: 526px; width: 291px;
    font-family: "Montserrat", sans-serif; font-weight: 600; font-size: 13.4px; line-height: 17px; color: var(--white); text-align: justify; }

  .spine-title, .spine-author { position: absolute; left: 50%; white-space: nowrap; color: var(--cream);
    transform-origin: 0 0; }
  .spine-title { top: 22px; font-family: "Cinzel", serif; font-size: 32px; transform: rotate(90deg) translateY(-50%); }
  .spine-author { top: 626px; font-family: "Josefin Sans", sans-serif; font-weight: 600; font-size: 13px; letter-spacing: 4px;
    transform: rotate(90deg) translateY(-50%); }

  .front-title { position: absolute; left: 50px; width: 490px; top: 38px; }
  .front-title .t1 { font-size: 68px; line-height: 74px; }
  .front-title .t2 { font-size: 64px; line-height: 78px; }
  .front-title .t3 { font-size: 118px; line-height: 128px; }
  .subtitle { position: absolute; left: 50px; width: 490px; top: 330px; text-align: center;
    font-family: "Cinzel", serif; font-size: 34px; color: var(--cream); }
  .author-name { position: absolute; left: 50px; width: 490px; top: 796px; text-align: center;
    font-family: "Josefin Sans", sans-serif; font-weight: 600; font-size: 26px; letter-spacing: 6px; color: var(--cream); }
</style>
</head>
<body>
<main class="cover">
  <div class="cover-art" role="img" aria-label="Dusk scene of a long road lined with red stone temples under a starry sky, a woman in a marigold dress walking toward the glowing horizon"></div>

  <section class="back-cover">
    <h2 class="title back-title"><span class="t1">WHERE THE</span><span class="t2">LANTERN</span><span class="t3">FADES</span></h2>
    <ul class="blurbs">
      <li>Lorem ipsum dolor sit amet, consectetur adipiscing elit, sed do eiusmod tempor incididunt ut labore et dolore magna aliqua. Quis ipsum suspendisse ultrices gravida. Risus commodo viverra maecenas accumsan lacus vel facilisis.</li>
      <li class="highlight">Lorem ipsum dolor sit amet, consectetur adipiscing elit, sed do eiusmod tempor incididunt ut labore et dolore magna aliqua</li>
      <li>Lorem ipsum dolor sit amet, consectetur adipiscing elit, sed do eiusmod tempor incididunt ut labore et dolore magna aliqua. Quis ipsum suspendisse ultrices gravida. Risus commodo viverra maecenas accumsan lacus vel facilisis.</li>
    </ul>
    <div class="divider"></div>
    <h3 class="about-heading">ABOUT THE AUTHOR</h3>
    <div class="author-photo" role="img" aria-label="Portrait photograph of the author wearing a white shawl"></div>
    <p class="author-bio">Carla Serena Tovi dolor sit amet, consectetur adipiscing elit, sed do eiusmod tempor incididunt ut labore et dolore magna aliqua. Quis ipsum suspendisse ultrices gravida. Risus commodo viverra maecenas accumsan lacus vel facilisis suspendisse ultrices gravida. Risus commodo viverra maecenas accumsan lacus vel facilisis.</p>
  </section>

  <section class="spine">
    <span class="spine-title">WHERE THE LANTERN FADES</span>
    <span class="spine-author">CARLA SERENA TOVI</span>
  </section>

  <section class="front-cover">
    <h1 class="title front-title"><span class="t1">WHERE THE</span><span class="t2">LANTERN</span><span class="t3">FADES</span></h1>
    <p class="subtitle">A Sacred Wandering</p>
    <p class="author-name">CARLA SERENA TOVI</p>
  </section>
</main>
</body>
</html>
```